Spy/Espionage/Counterintelligence Membership Community Needs a PowerPoint Template

We need a powerpoint template for one of our business verticals focused on spies, espionage, and counterintelligence. The name of it is "Brass Lantern Guild" and the logo is attached. Brass Lantern Guild is a community that connects people with experts in espionage and counterintelligence through an online social network, as well as in-person events. We would like to see designs that incorporate the red and black of the logo. The design should communicate mystery/suspense and peak curiosity.

Target Market(s)

Late 20s to baby boomers, male

Industry/Entity Type

Social Club

Font styles to use
Sans Serif

Colors
ec1f27
000000
ffffff

Requirements
Must have
• A user-friendly ppt template file. Incorporate basic fonts that don't have to be installed on every computer for presentations. A cover slide and a basic inside slide. A white background. I will also need graphic source files.
Nice to have
• Plenty of space for slide title and body content. Logo on every slide.
Should not have
• Inconsistency with fonts. Misalignment of images.

```html
<!DOCTYPE html>
<html lang="en">
<head>
<meta charset="utf-8">
<title>Brass Lantern Guild – Presentation Template</title>
<link href="https://fonts.googleapis.com/css2?family=PT+Sans+Narrow:wght@400;700&family=PT+Sans:ital,wght@0,400;1,400&display=swap" rel="stylesheet">
<style>
:root{
  --stage:#1d2224;
  --red:#d3121a;
  --red-deep:#8e0b10;
  --red-dark:#6a0609;
  --title-red:#8f0e12;
  --ink:#1a1a1a;
  --white:#ffffff;
  --paper:#fbf9f8;
  --sky:#dcedf8;
  --btn:#1e1e1e;
}
*{box-sizing:border-box;margin:0;padding:0}
html,body{width:1200px;height:900px;overflow:hidden;background:var(--stage)}
body{position:relative;font-family:"PT Sans Narrow",sans-serif;color:var(--ink)}
.slide{position:absolute;width:585px;height:437px;overflow:hidden;background:radial-gradient(ellipse at 50% 40%,var(--white),var(--paper) 70%,#f1ecea)}
.s1{left:10px;top:8px}.s2{left:605px;top:8px}.s3{left:10px;top:455px}.s4{left:605px;top:455px}

/* cover */
.cover-band{position:absolute;left:0;top:0;width:100%;height:256px;background:linear-gradient(180deg,var(--red-deep),var(--red) 55%,#b80e15)}
.cover-rule{position:absolute;left:0;top:256px;width:100%;height:5px;background:#000}
.cover-sky{position:absolute;left:0;top:261px;width:100%;height:136px;background:linear-gradient(180deg,var(--sky),#f3f9fd)}
.cover-disc{position:absolute;left:22px;top:155px;width:210px;height:210px;border-radius:50%;background:var(--red);border:9px solid #000;box-shadow:0 0 0 4px var(--white)}
.cover-title{position:absolute;right:34px;top:92px;font-weight:700;font-size:35px;color:var(--white)}
.cover-sub{position:absolute;right:34px;top:140px;width:360px;text-align:right;font-size:13.5px;line-height:20px;color:var(--white)}
.cover-name{position:absolute;right:40px;top:300px;font-size:40px;color:var(--ink)}

/* inner */
.flag{position:absolute;left:0;top:12px}
.slide-title{position:absolute;left:30px;top:10px;font-weight:700;font-size:26px;color:var(--title-red)}
.ghost-disc{position:absolute;left:183px;top:120px;width:215px;height:215px;border-radius:50%;border:10px solid rgba(211,18,26,.07);background:rgba(211,18,26,.04)}
.corner-name{position:absolute;right:12px;top:362px;font-size:22px;color:var(--ink)}

.section-head{position:absolute;left:43px;top:70px;font-weight:700;font-size:17px;color:var(--title-red)}
.ticks{position:absolute;left:45px;top:98px;list-style:none;font-size:13px;line-height:19px}
.ticks li{position:relative;padding-left:20px}
.ticks svg{position:absolute;left:0;top:3px}
.s3 .ticks{width:470px}
.photo{position:absolute;left:185px;top:88px;width:370px;height:280px;background:linear-gradient(180deg,rgba(120,120,130,.35),rgba(60,60,70,.55) 55%,rgba(255,255,255,0))}

/* footer */
.footer{position:absolute;left:0;top:397px;width:100%;height:40px;background:linear-gradient(180deg,var(--red),var(--red-dark));border-top:2px solid #000}
.page-no{position:absolute;left:15px;top:7px;width:30px;height:25px;background:var(--btn);color:var(--white);font-family:"PT Sans",sans-serif;font-size:15px;text-align:center;line-height:25px;border-radius:2px}
.footer-text{position:absolute;left:63px;top:11px;font-family:"PT Sans",sans-serif;font-style:italic;font-size:13px;color:var(--white)}
.s1 .footer-text{left:92px;font-weight:700}
.btn{position:absolute;top:7px;height:26px;background:var(--btn);color:var(--white);font-family:"PT Sans",sans-serif;font-size:12px;line-height:26px;text-align:center}
.btn-back{right:64px;width:48px;clip-path:polygon(10px 0,100% 0,100% 100%,10px 100%,0 50%)}
.btn-next{right:14px;width:46px;clip-path:polygon(0 0,calc(100% - 10px) 0,100% 50%,calc(100% - 10px) 100%,0 100%)}
.btn-start{right:14px;width:44px;border-radius:3px}
</style>
</head>
<body>
<svg width="0" height="0" style="position:absolute">
  <defs>
    <symbol id="tick" viewBox="0 0 13 13"><rect x="1" y="2" width="10" height="10" fill="none" stroke="#1a1a1a" stroke-width="1.2"/><path d="M3 6.5l3 3L12.5 1" fill="none" stroke="#8f0e12" stroke-width="2"/></symbol>
    <symbol id="flag" viewBox="0 0 22 28"><polygon points="0,0 22,0 22,28 0,28 10,14" fill="#c8121a"/></symbol>
  </defs>
</svg>

<section class="slide s1">
  <div class="cover-band"></div><div class="cover-rule"></div><div class="cover-sky"></div>
  <h1 class="cover-title">Project Title Here</h1>
  <p class="cover-sub">Subtext here Subtext here Subtext here Subtext here Subtext here Subtext here Subtext here Subtext here</p>
  <div class="cover-disc"></div>
  <div class="cover-name">Brass Lantern Guild</div>
  <footer class="footer"><span class="page-no">01</span><span class="footer-text">09/06/15</span><span class="btn btn-start">Start</span></footer>
</section>

<section class="slide s2">
  <svg class="flag" width="22" height="28"><use href="#flag"/></svg>
  <h2 class="slide-title">Presentation Title</h2>
  <div class="ghost-disc"></div>
  <div class="corner-name">Brass Lantern Guild</div>
  <footer class="footer"><span class="page-no">02</span><span class="footer-text">tagline/slogan about your company</span><span class="btn btn-back">Back</span><span class="btn btn-next">Next</span></footer>
</section>

<section class="slide s3">
  <svg class="flag" width="22" height="28"><use href="#flag"/></svg>
  <h2 class="slide-title">Presentation Title</h2>
  <div class="ghost-disc"></div>
  <h3 class="section-head">Something About Your Business</h3>
  <ul class="ticks">
    <li><svg width="13" height="13"><use href="#tick"/></svg>High volume local boutique real estate company</li>
    <li><svg width="13" height="13"><use href="#tick"/></svg>Specialize in selling homes throughout the San Francisco Bay Area</li>
    <li><svg width="13" height="13"><use href="#tick"/></svg>Focus on modern marketing techniques and thinking outside the box</li>
    <li><svg width="13" height="13"><use href="#tick"/></svg>“High Tech and High Touch” approach to real estate</li>
    <li><svg width="13" height="13"><use href="#tick"/></svg>Certified Green Business Everything is done and stored online. No File Cabinets in our offices!</li>
    <li><svg width="13" height="13"><use href="#tick"/></svg>Exceptional web presence far beyond other local real estate companies</li>
    <li><svg width="13" height="13"><use href="#tick"/></svg>Clean, streamline, and hip marketing materials</li>
    <li><svg width="13" height="13"><use href="#tick"/></svg>A company constantly looking into the latest real estate trends, tools, and technology to better assist their agents and clients sell homes in the modern world, all while embracing tried and true real estate values and practices as well</li>
    <li><svg width="13" height="13"><use href="#tick"/></svg>Leading authority for architectural homes and recognized world wide</li>
    <li><svg width="13" height="13"><use href="#tick"/></svg>Not Just Modern Homes! We focus on Modern Real Estate<br>Practices through and through.</li>
  </ul>
  <div class="corner-name">Brass Lantern Guild</div>
  <footer class="footer"><span class="page-no">03</span><span class="footer-text">tagline/slogan about your company</span><span class="btn btn-back">Back</span><span class="btn btn-next">Next</span></footer>
</section>

<section class="slide s4">
  <svg class="flag" width="22" height="28"><use href="#flag"/></svg>
  <h2 class="slide-title">Presentation Title</h2>
  <div class="ghost-disc"></div>
  <h3 class="section-head">Our Services</h3>
  <ul class="ticks">
    <li><svg width="13" height="13"><use href="#tick"/></svg>Handymen</li>
    <li><svg width="13" height="13"><use href="#tick"/></svg>Contractors</li>
    <li><svg width="13" height="13"><use href="#tick"/></svg>Stagers</li>
    <li><svg width="13" height="13"><use href="#tick"/></svg>Painters</li>
    <li><svg width="13" height="13"><use href="#tick"/></svg>Cleaners</li>
    <li><svg width="13" height="13"><use href="#tick"/></svg>Movers</li>
    <li><svg width="13" height="13"><use href="#tick"/></svg>Storage companies</li>
    <li><svg width="13" height="13"><use href="#tick"/></svg>Landscapers</li>
    <li><svg width="13" height="13"><use href="#tick"/></svg>Estate Sale Professionals</li>
    <li><svg width="13" height="13"><use href="#tick"/></svg>Lawyers</li>
    <li><svg width="13" height="13"><use href="#tick"/></svg>Mortgage Brokers</li>
    <li><svg width="13" height="13"><use href="#tick"/></svg>Inspectors</li>
  </ul>
  <div class="photo" role="img" aria-label="Group photo of business professionals and tradespeople standing together"></div>
  <div class="corner-name">Brass Lantern Guild</div>
  <footer class="footer"><span class="page-no">04</span><span class="footer-text">tagline/slogan about your company</span><span class="btn btn-back">Back</span><span class="btn btn-next">Next</span></footer>
</section>
</body>
</html>
```